Brel Fosk Painting, Eco and Non toxic painting client information brochure.

Brel fosk painting is a painting company that specialises in eco and non toxic paints. This brochure will be left with the client after the initial meeting to explain about my business and hopefully win the job. By reading the text i have provided (see attachment) you can get a better understanding of what we do.
The brochure should be fresh and clean looking, complimenting the Brel Fosk Painting logo and the text provided.
This will be printed onto a recycled paper.
Text and font must clear and easy to read.

Please have a look at my web page. I will be redoing this soon as well but this will give you some ideas of where I'm at.

Would like some picture but not sure what.
I have attached some pics but they don't have to be use
Updates

Hi peeps,

Thanks for all the great designs and sorry i haven't got back to you sooner.
been a bit busy.
Tomorrow i hope to be able to sit down and have a good look at what everybody has done.
Thanks again i really appreciate the effort.

kind regards oswin 

hi designers,

Just sat down and had a good look at the designs sent in and there are some crackers.
Its going to be very difficult to choose. I have only 1 day left before it closes so ill wait till then to see if there are any more submissions come in then ill get back to everybody.
Thanks again for your time and effort.

kind regards oswin 

Hi too all you designers that have worked on my project. 

I am always amazed at all the different designs that come through. Super work guys and girls. 
I have narrowed it down to a couple of designs.
Ill be making the decision tonight.
Thanks again to you all and i really appreciate all the hard work.
I will be doing another brochure in the future for more architecture / builder focus and there were a few designs that would work perfectly for this.

Kinds regards oswin  

Target Market(s)

The work we do is mainly residential repaints, family homes
Mostly I am dealing with the wife of the family or female designers/architects

Industry/Entity Type

Painting

Requirements
Must have
• Company logo, either white or black version what ever suits best.
Text that has been provided.
Brochure will be 1 page A 4, folded into 3 parts both sides.
Front page must have logo and
SPECIALSING IN:
NON TOXIC
ECO FRIENDLY &
HEAT REFLECTIVE PAINTS
Phone 041 382 6190
Painting@brelfosk.biz
www.brelfosk.biz

```html
<!DOCTYPE html>
<html lang="en">
<head>
<meta charset="utf-8">
<title>Brel Fosk Painting – Client Information Brochure (Inside)</title>
<link href="https://fonts.googleapis.com/css2?family=Questrial&display=swap" rel="stylesheet">
<style>
  :root {
    --teal: #1aa3ad;
    --teal-soft: rgba(26, 163, 173, 0.35);
    --teal-clear: rgba(26, 163, 173, 0);
    --orange: #d9622b;
    --orange-soft: rgba(217, 98, 43, 0.45);
    --orange-clear: rgba(217, 98, 43, 0);
    --paper: #ffffff;
    --heading-text: #ffffff;
  }
  * { box-sizing: border-box; margin: 0; padding: 0; }
  html, body { width: 1200px; height: 848px; overflow: hidden; background: var(--paper); }
  .brochure {
    position: relative;
    width: 1200px;
    height: 848px;
    font-family: "Questrial", "Century Gothic", sans-serif;
    font-size: 10.5px;
    line-height: 15.1px;
    letter-spacing: 0.45px;
  }

  /* Soft colour bands between the panels */
  .colour-band { position: absolute; top: 0; height: 848px; }
  .colour-band--left {
    left: 252px; width: 132px;
    background: linear-gradient(to right, var(--teal-clear) 0%, var(--teal-soft) 28%, var(--teal) 58%, var(--teal) 100%);
  }
  .colour-band--middle {
    left: 640px; width: 144px;
    background: linear-gradient(to right, var(--orange-clear) 0%, var(--orange-soft) 25%, var(--orange) 58%, var(--orange) 100%);
  }
  .colour-band--right {
    left: 1064px; width: 136px;
    background: linear-gradient(to right, var(--teal-clear) 0%, var(--teal-soft) 28%, var(--teal) 58%, var(--teal) 100%);
  }

  .panel { position: absolute; top: 41px; }
  .panel--business { left: 40px; width: 202px; color: var(--teal); }
  .panel--owner { left: 425px; width: 208px; color: var(--orange); }
  .panel--vocs { left: 824px; width: 216px; color: var(--teal); }

  .section-heading {
    display: block;
    color: var(--heading-text);
    font-size: 14px;
    font-weight: 400;
    line-height: 31px;
    height: 31px;
    padding: 0 9px;
    text-transform: uppercase;
    letter-spacing: 0.3px;
  }
  .panel--business .section-heading { background: var(--teal); width: 207px; }
  .panel--owner .section-heading { background: var(--orange); width: 205px; }
  .panel--vocs .section-heading { background: var(--teal); width: 86px; }

  .section-body { margin-top: 22px; }
  .section--hiring { margin-top: 22px; }
  .section--green { margin-top: 28px; }
  .vocs-subtitle { font-style: italic; margin-top: 24px; letter-spacing: 0.6px; }
  .vocs-body { margin-top: 16px; }
</style>
</head>
<body>
<main class="brochure">
  <div class="colour-band colour-band--left" role="img" aria-label="Soft teal painted band"></div>
  <div class="colour-band colour-band--middle" role="img" aria-label="Soft orange painted band"></div>
  <div class="colour-band colour-band--right" role="img" aria-label="Soft teal painted band"></div>

  <section class="panel panel--business">
    <h2 class="section-heading">About the business</h2>
    <p class="section-body">At Brel Fosk Painting we provide a high-quality service and exceptional craftsmanship for both domestic and commercial projects. We are proud to say we are making our work practices and business support processes more sustainable.<br>
    We want to be sure we are doing our part to reduce our carbon footprint. We take the time to research alternative eco painting products and processes.<br>
    We can also provide you with information about the products and why we use them.<br>
    All our jobs are professionally finished utilising only the best tools and products available.<br>
    We aim to limit the interruption to clients and their families as a result of our work; safety is paramount. We make sure that you are satisfied with the work done and will communicate with you throughout the job.<br>
    Brel Fosk Painting is dedicated to learning, understanding and implementing new products and techniques that will be safer for the environment and your family. All this is done at a competitive price.</p>
  </section>

  <section class="panel panel--owner">
    <div class="section">
      <h2 class="section-heading">About the owner</h2>
      <p class="section-body">Brel Fosk has been painting for over 20 years.<br>
      He is an accredited Green Painter and is often called upon by architects and builders to provide advice on sustainable products and methods.</p>
    </div>
    <div class="section section--hiring">
      <h2 class="section-heading">Hiring a professional</h2>
      <p class="section-body">Hiring a professional painter is never an easy decision and one not to be taken lightly.<br>
      Painting is a highly skilled trade and it takes considerable experience and expertise to obtain a high quality finish.</p>
    </div>
    <div class="section section--green">
      <h2 class="section-heading">Going green</h2>
      <p class="section-body">We can help you make smart decisions about creating a better environment and further minimizing any risk for your family and the spaces we live in.<br>
      This can be achieved reducing the amount of VOCs (volatile organic compounds) by selecting the correct products.</p>
    </div>
  </section>

  <section class="panel panel--vocs">
    <h2 class="section-heading">VOCs</h2>
    <p class="vocs-subtitle">(VOLATILE ORGANIC COMPOUNDS)</p>
    <p class="vocs-body">VOCs are hazardous chemicals that are emitted from paints.<br>
    This occurs even after the paint has dried; paints can continue too emit VOCs for several years after application.<br>
    By using low VOC emitting paints, fewer chemicals are released than traditional paints.<br>
    In choosing a zero VOC option, you will experience no odour after the paint has dried and will be helping improve air quality both inside and outside your home or business.<br>
    At Brel Fosk Painting we choose to use these products and a green business approach because we care about our clients, workers and the overall environment.<br>
    We can help make a difference, not just by changing the colour of your home or business but by giving you a better, safer environment in which to live and work.</p>
  </section>
</main>
</body>
</html>
```